Packaging design - PROTEIN BALLS

PACKAGING
The packaging is a round carton roll, size: Ø73x180 mm, mockup sample enclosed, The label on the carton roll should have a size of 225x178 mm (width x height)

PRODUCT
Chrunchy, cheesy PROTEIN BALLS (100% pure cheese) with a huge amount of protein (65%), a lot of calcium and very low carbogydrates (3%). Diameter about 1.5 cm.

DESIGN
Since our customers are very sporty people, runner, bodybuilder, etc. The design must fit to this sporty customer segment.

FILES
We need the open data for InDesign with all fonts and pictures. If there are licenses tu buy, we will do it.

SUMMARY
1. SNACK
• Crunchy cheese balls with a diameter of about 1.5cm
• 3 different flavors: "Swiss Alpine Salt", "Provencale" and "Hot Chili"
• High in Protein (65%) and Calcium (2%)
• Low in carbohydrates (3%)

2. PACKAGING
• Carton roll, size: Ø73x180 mm
• Background can be every color, but we think a black one will be high premium.
• Maybe different sports are represented in the background, maybe also cheese
• Be creative
• Label applied, size: 225x178 mm

3. DESIGN
• Product name = (Cheese) PROTEIN BALLS
• 3 different colors for the 3 flavors "Swiss Alpine Salt", "Provencale" and "Hot Chili"
• HighProtein, High Calcium and LowCarb must be pointed out on the front
• Swissness: Swiss made must be pointed out
• fresh and young design, most customers are sporty people, pumper with a strong body awareness

Target Market(s)

TARGET CUSTOMER
Our main customers are extremely sporty people, who work very hard on their muscles and fitness, most of them are runners, cross fitnesser, bodybuilders, etc We will launch the product in fitness centers, in supplement shops and we are planning to make some stories with sporty influencer.

Font styles to use
Serif
Sans Serif

Requirements
Must have
• Cheese, naturalness, healthy, PROTEIN balls, muscles, Swissness must showed on the product.

```html
<!DOCTYPE html>
<html lang="en">
<head>
<meta charset="utf-8">
<title>Cheese Protein Balls – Flavour Labels</title>
<link rel="stylesheet" href="https://fonts.googleapis.com/css2?family=Bebas+Neue&family=Oswald:wght@500&family=Yellowtail&family=Amatic+SC:wght@700&display=swap">
<style>
  :root {
    --page: #ffffff;
    --label-dark: #333436;
    --label-mid: #4a4b4e;
    --label-band: #3c3d40;
    --ink-light: #f1f1ef;
    --cheese-gold: #cbbd96;
    --sketch: #6a6b6e;
    --swiss-red: #d52b1e;
    --chili: #b8322f;
    --provence: #7c9a3c;
    --alpine: #2f95d6;
    --badge-fill: #dedede;
  }
  * { margin: 0; padding: 0; box-sizing: border-box; }
  html, body { width: 1200px; height: 1200px; overflow: hidden; background: var(--page); }
  .shelf { position: relative; width: 1200px; height: 1200px; }

  .label {
    position: absolute; top: 258px; width: 244px; height: 692px;
    background: linear-gradient(90deg, var(--label-dark) 0%, var(--label-mid) 55%, var(--label-dark) 100%);
    overflow: hidden;
    color: var(--ink-light);
    text-align: center;
  }
  .label--chili { left: 114px; }
  .label--provence { left: 466px; --accent: var(--provence); }
  .label--alpine { left: 818px; --accent: var(--alpine); }
  .label--chili { --accent: var(--chili); }

  .label__band {
    position: absolute; left: 0; right: 0; top: 34px; bottom: 34px;
    background: linear-gradient(90deg, var(--label-band), #46474a 60%, var(--label-band));
  }

  .origin {
    position: absolute; top: 58px; left: 0; right: 0;
    display: flex; justify-content: center; align-items: center; gap: 8px;
    font-family: "Oswald", sans-serif; font-weight: 500; font-size: 16px; letter-spacing: 1.5px;
  }
  .origin__flag { width: 28px; height: 24px; }

  .mountain-art {
    position: absolute; top: 92px; left: 10px; width: 230px; height: 210px;
    background: radial-gradient(ellipse at 45% 45%, rgba(120,121,124,0.55), rgba(80,81,84,0) 70%);
  }

  .product-kind {
    position: absolute; top: 222px; left: 0; right: 0;
    font-family: "Yellowtail", cursive; font-size: 44px; color: var(--cheese-gold); line-height: 1;
  }
  .product-name {
    position: absolute; top: 276px; left: 0; right: 0;
    font-family: "Bebas Neue", sans-serif; font-size: 72px; line-height: 68px; letter-spacing: 1px;
  }
  .audience {
    position: absolute; top: 430px; left: 0; right: 0;
    font-family: "Oswald", sans-serif; font-weight: 500; font-size: 18px; letter-spacing: 1.5px;
  }

  .flavour {
    position: absolute; top: 482px; left: 32px; width: 182px; height: 46px;
    background: var(--accent);
    font-family: "Yellowtail", cursive; font-size: 34px; line-height: 46px; color: var(--ink-light);
    white-space: nowrap;
  }
  .label--alpine .flavour { left: 30px; width: 186px; font-size: 25px; }
  .flavour-art {
    position: absolute; top: 480px; right: 4px; width: 62px; height: 82px;
    border-radius: 40%;
    background: radial-gradient(circle, var(--accent) 0%, rgba(0,0,0,0) 70%);
    opacity: 0.8;
  }
  .label--alpine .flavour-art { background: radial-gradient(circle, #d9d9d9 0%, rgba(0,0,0,0) 70%); }

  .claims {
    position: absolute; top: 568px; left: 0; right: 0;
    display: flex; justify-content: center; gap: 10px;
  }
  .claim {
    width: 52px; height: 52px; border-radius: 50%;
    border: 2px solid var(--ink-light);
    background: var(--badge-fill); color: var(--accent);
    display: flex; align-items: center; justify-content: center;
    font-family: "Amatic SC", sans-serif; font-weight: 700; font-size: 13px; line-height: 12px;
  }
  .claim--lead { background: var(--accent); color: var(--ink-light); }
</style>
</head>
<body>
<main class="shelf">

  <section class="label label--chili">
    <div class="label__band"></div>
    <div class="origin">SWISS MADE
      <svg class="origin__flag" viewBox="0 0 28 24"><rect width="28" height="24" fill="var(--swiss-red)"/><path d="M12 5h4v5h5v4h-5v5h-4v-5H7v-4h5z" fill="#fff"/></svg>
    </div>
    <div class="mountain-art" role="img" aria-label="Pencil sketch of an alpine mountain peak"></div>
    <div class="product-kind">Cheese</div>
    <h1 class="product-name">PROTEIN<br>BALLS</h1>
    <div class="audience">- FOR ATHLETES -</div>
    <div class="flavour-art" role="img" aria-label="Illustration of red chili peppers"></div>
    <div class="flavour">Hot Chili</div>
    <div class="claims">
      <div class="claim claim--lead">LOW<br>CARB</div>
      <div class="claim">HIGH<br>PROTEIN<br>65%</div>
      <div class="claim">HIGH<br>CALCIUM</div>
    </div>
  </section>

  <section class="label label--provence">
    <div class="label__band"></div>
    <div class="origin">SWISS MADE
      <svg class="origin__flag" viewBox="0 0 28 24"><rect width="28" height="24" fill="var(--swiss-red)"/><path d="M12 5h4v5h5v4h-5v5h-4v-5H7v-4h5z" fill="#fff"/></svg>
    </div>
    <div class="mountain-art" role="img" aria-label="Pencil sketch of an alpine mountain peak"></div>
    <div class="product-kind">Cheese</div>
    <h1 class="product-name">PROTEIN<br>BALLS</h1>
    <div class="audience">- FOR ATHLETES -</div>
    <div class="flavour-art" role="img" aria-label="Illustration of fresh basil leaves"></div>
    <div class="flavour">Provencale</div>
    <div class="claims">
      <div class="claim claim--lead">LOW<br>CARB</div>
      <div class="claim">HIGH<br>PROTEIN<br>65%</div>
      <div class="claim">HIGH<br>CALCIUM</div>
    </div>
  </section>

  <section class="label label--alpine">
    <div class="label__band"></div>
    <div class="origin">SWISS MADE
      <svg class="origin__flag" viewBox="0 0 28 24"><rect width="28" height="24" fill="var(--swiss-red)"/><path d="M12 5h4v5h5v4h-5v5h-4v-5H7v-4h5z" fill="#fff"/></svg>
    </div>
    <div class="mountain-art" role="img" aria-label="Pencil sketch of an alpine mountain peak"></div>
    <div class="product-kind">Cheese</div>
    <h1 class="product-name">PROTEIN<br>BALLS</h1>
    <div class="audience">- FOR ATHLETES -</div>
    <div class="flavour-art" role="img" aria-label="Illustration of a salt shaker"></div>
    <div class="flavour">Swiss Alpine Salt</div>
    <div class="claims">
      <div class="claim claim--lead">LOW<br>CARB</div>
      <div class="claim">HIGH<br>PROTEIN<br>65%</div>
      <div class="claim">HIGH<br>CALCIUM</div>
    </div>
  </section>

</main>
</body>
</html>
```